Local Roofing Company Billboard Design

We need a billboard design for an 8' x 32' billboard. This billboard would need to be easily readable and stand out well.
I have uploaded a design that we like - simple, readable, and gets the point across. We do NOT want the $1000 off offer included.
We are looking for a black background with white copy so it will stand out. We want the following on the billboard:
Brindlewick Roofing logo
brindlewick-roofing.example (optional)
555.214.7730 (mandatory)
Photo is optional, depends on how it all lays out
Production file must comply with layout requirements (uploaded).
Target Market(s)
Homeowners
Font styles to use
Other font styles liked:
- match font from logo
Colors
Designer to choose colors to be used in the design.
Requirements
Must have
- Black background, white copy, logo must be large and legible. Colors used must match our logo colors.

```html
<!DOCTYPE html>
<html lang="en">
<head>
<meta charset="utf-8">
<title>Brindlewick Roofing Billboard</title>
<link rel="stylesheet" href="https://fonts.googleapis.com/css2?family=Bebas+Neue&family=Montserrat:wght@500;700&display=swap">
<style>
  :root {
    --page: #ffffff;
    --ink: #000000;
    --paper: #ffffff;
    --brand-orange: #e4561f;
    --sky-deep: #2f67c4;
    --sky-light: #9cc2ea;
  }
  * { box-sizing: border-box; margin: 0; padding: 0; }
  html, body {
    width: 1200px; height: 1051px; overflow: hidden;
    background: var(--page);
  }
  .billboard {
    position: absolute; left: 40px; top: 385px;
    width: 1120px; height: 280px;
    box-shadow: 0 18px 40px rgba(0,0,0,.18);
    overflow: hidden;
    background: var(--ink);
  }
  .billboard-shapes { position: absolute; inset: 0; }
  .brand-name {
    position: absolute; left: 560px; right: 0; top: 58px;
    text-align: center;
    font-family: "Montserrat", sans-serif; font-weight: 700;
    font-size: 44px; color: var(--paper); letter-spacing: .5px;
    white-space: nowrap;
  }
  .website {
    position: absolute; left: 30px; top: 224px;
    display: flex; align-items: center; gap: 14px;
    font-family: "Montserrat", sans-serif; font-weight: 500;
    font-size: 20px; line-height: 1; color: var(--paper); letter-spacing: .4px;
    white-space: nowrap;
  }
  .phone {
    position: absolute; left: 508px; top: 178px;
    display: flex; align-items: center; gap: 18px;
    font-family: "Bebas Neue", sans-serif;
    font-size: 96px; line-height: 1; color: var(--paper);
    letter-spacing: 5px;
    white-space: nowrap;
  }
</style>
</head>
<body>
  <section class="billboard">
    <svg class="billboard-shapes" width="1120" height="280" viewBox="0 0 1120 280">
      <defs>
        <linearGradient id="skyFill" x1="0" y1="0" x2="0.3" y2="1">
          <stop offset="0" stop-color="var(--sky-light)"/>
          <stop offset="0.6" stop-color="var(--sky-deep)"/>
          <stop offset="1" stop-color="#1d3f86"/>
        </linearGradient>
      </defs>
      <rect class="photo-area" role="img" aria-label="Photo of a roofer in a hard hat working on a metal roof under a blue sky"
            x="0" y="0" width="640" height="210" fill="url(#skyFill)"/>
      <polygon class="website-band" points="0,204 480,204 424,280 0,280" fill="var(--ink)"/>
      <polygon class="diagonal-accent" points="611,0 621,0 508,161 498,161" fill="var(--brand-orange)"/>
      <polygon class="brand-panel" points="621,0 1120,0 1120,161 508,161" fill="var(--ink)"/>
      <polygon class="diagonal-divider" points="498,161 508,161 424,280 412,280" fill="var(--paper)"/>
      <polygon class="phone-band" points="508,161 1120,161 1120,280 424,280" fill="var(--brand-orange)"/>
    </svg>

    <div class="brand-name">Brindlewick Roofing</div>

    <div class="website">
      <svg class="icon-laptop" width="30" height="24" viewBox="0 0 36 28" aria-hidden="true">
        <rect x="5" y="2" width="26" height="18" fill="none" stroke="#fff" stroke-width="3.5"/>
        <rect x="1" y="22" width="34" height="4" fill="#fff"/>
      </svg>
      <span>brindlewick-roofing.example</span>
    </div>

    <div class="phone">
      <svg class="icon-phone" width="50" height="50" viewBox="0 0 50 50" aria-hidden="true">
        <path d="M12 6 l7 10 -4 5 c2 6 7 11 13 13 l5 -4 10 7 -4 7 c-16 1 -33 -16 -33 -32 z" fill="#fff"/>
        <path d="M28 10 a12 12 0 0 1 12 12" fill="none" stroke="#fff" stroke-width="3.5" stroke-linecap="round"/>
        <path d="M29 2 a19 19 0 0 1 19 19" fill="none" stroke="#fff" stroke-width="3.5" stroke-linecap="round"/>
      </svg>
      <span>555-214-7730</span>
    </div>
  </section>
</body>
</html>
```